Store Front Signage for an Upscale Cake & Dessert Bakery

We need a design for store front windows. We are a 12 year old bakery specializing in cakes, cupcakes, cookies, pies, and other desserts. We recently moved to a high traffic location.. and we would like to boost our visual presence; we can be seen from the main road but are competing with other businesses for attention. Attached is a photo of our store front with posters but this signage will be for window film for the entire window span. (see the store front to the left of the photo to see the green and yellow as a film example)
Our logo and store sign (not like in photo, that is showing more red) are in shades of pink. The most visible part of the signage is in the upper third to upper half of the 60" panels.
The signs in the window currently say Life's Short. Eat Cake.
We now use Enjoy Life. Eat Cake.
The design should span all the windows and door -- this can be individual panels or one design that covers all panels. I have pink and greys chosen but please DO NOT let this constrain you. The inside of the bakery has grey floors and walls. white cabinetry, black granite countertops. The only thing with color is the baked goods and display cakes, pictures of cakes, the logo and menu and employee shirts.

Target Market(s)

we are located at a busy intersection --- we would like to capture the attention of people in cars as they pass by and entice them to stop in

Font styles to use
Serif
Sans Serif

Colors
d3d3d3
757575
ffffff
e24197
e667a6
eea4c8
f9d9e8

Requirements
Must have
• I would like the design to be easily discernible at the road way that is about 75 feet from store front. If you look at the photos I provide, note that the font size that is easily readable from the road are the ones in the top panes (although the shadow from the building makes them difficult to see -- the best visibility is the top 1/3 of the 60" panels.
Nice to have
• would like to have some non-photo graphics of a cake ( like a birthday cake), tiered cake, cupcakes, and cookies or pie for the panels --- but DO NOT let this constrain you. I need something to grab attention while cars are stopped at the nearby traffic light.
• If this design works well... I will be changing the panel on a seasonal basis
Should not have
• words that cannot be read from a distance.

```html
<!DOCTYPE html>
<html lang="en">
<head>
<meta charset="utf-8">
<title>Rosalind's Bake House – Storefront Window Film</title>
<link rel="stylesheet" href="https://fonts.googleapis.com/css2?family=Cormorant+Garamond:wght@700&family=Fredoka:wght@500;600&family=Oswald:wght@300;500;700&family=Montserrat:wght@600;800&family=Fira+Sans:ital,wght@0,700;1,600&display=swap">
<style>
  :root {
    --bg: #ececec;
    --frame: #1c1c1c;
    --teal-light: #36a9c6;
    --teal-mid: #1f6e83;
    --teal-dark: #132a31;
    --magenta: #961251;
    --blush: #eeb6cb;
    --white: #ffffff;
    --hours-red: #e0201a;
    --lamp: #ffd23a;
  }
  * { margin: 0; padding: 0; box-sizing: border-box; }
  html, body { width: 1200px; height: 1000px; overflow: hidden; background: var(--bg); }
  .canvas { position: relative; width: 1200px; height: 1000px; }

  .storefront { position: absolute; left: 38px; top: 224px; width: 1124px; height: 552px; background: var(--frame); }

  .pane { position: absolute; }
  .pane--top { top: 9px; height: 140px; background: linear-gradient(180deg, var(--teal-mid) 0%, var(--teal-dark) 100%); overflow: hidden; }
  .pane--low { top: 159px; height: 384px; background: linear-gradient(180deg, var(--teal-light) 0%, var(--teal-mid) 35%, var(--teal-dark) 64%); overflow: hidden; }

  .awning { position: absolute; left: 0; top: 0; width: 100%; height: 45px; }

  .headline {
    position: absolute; left: 0; right: 0; top: 58px; text-align: center;
    font-family: "Cormorant Garamond", serif; font-weight: 700; font-size: 58px;
    color: var(--white); letter-spacing: 1px; line-height: 1;
  }

  .stripes { position: absolute; left: 0; right: 0; top: 245px; }
  .stripes .band-magenta { height: 36px; background: var(--magenta); }
  .stripes .band-dark { height: 9px; background: var(--frame); }
  .stripes .band-blush { height: 13px; background: var(--blush); }
  .stripes .band-white { height: 4px; background: var(--white); }
  .stripes .band-base { height: 77px; background: linear-gradient(180deg, var(--teal-light) 0%, var(--teal-dark) 100%); }

  .offer-list { position: absolute; left: 0; right: 0; top: 16px; text-align: center; color: var(--white); }
  .offer-list > div { line-height: 1; }
  .offer-list .custom { font-family: "Fredoka", sans-serif; font-weight: 600; font-size: 38px; line-height: 40px; transform: rotate(-9deg); display: inline-block; }
  .offer-list .cake { font-family: "Oswald", sans-serif; font-weight: 300; font-size: 26px; line-height: 28px; }
  .offer-list .holiday { font-family: "Oswald", sans-serif; font-weight: 700; font-size: 40px; line-height: 42px; letter-spacing: 1px; }
  .offer-list .desserts { font-family: "Oswald", sans-serif; font-weight: 300; font-size: 27px; line-height: 30px; letter-spacing: 8px; padding-left: 8px; }
  .offer-list .cupcakes { font-family: "Fredoka", sans-serif; font-weight: 600; font-size: 24px; line-height: 26px; }
  .offer-list .cookies { font-family: "Fredoka", sans-serif; font-weight: 500; font-size: 18px; line-height: 20px; letter-spacing: 2px; }
  .offer-list .amp { font-family: "Fredoka", sans-serif; font-weight: 600; font-size: 14px; line-height: 13px; }
  .offer-list .sweets { font-family: "Fredoka", sans-serif; font-weight: 600; font-size: 22px; line-height: 22px; transform: rotate(-6deg); display: inline-block; }

  .brand-name {
    position: absolute; left: 0; right: 0; top: 128px; text-align: center;
    font-family: "Montserrat", sans-serif; font-weight: 800; font-size: 24px; line-height: 1.15;
    color: var(--blush);
  }
  .brand-name .dot { display: block; width: 14px; height: 14px; border-radius: 50%; background: var(--blush); margin: 0 auto 10px; }

  .service { position: absolute; left: 0; right: 0; top: 38px; text-align: center; color: var(--white); line-height: 1; }
  .service .next { font-family: "Montserrat", sans-serif; font-weight: 800; font-size: 27px; }
  .service .pickup { font-family: "Oswald", sans-serif; font-weight: 500; font-size: 38px; }
  .service .available, .service .delivery { font-family: "Montserrat", sans-serif; font-weight: 800; font-size: 27px; }
  .service .order {
    display: inline-block; margin-top: 16px; width: 154px; padding: 3px 0;
    background: var(--white); color: var(--teal-dark);
    font-family: "Fira Sans", sans-serif; font-style: italic; font-weight: 600; font-size: 18px;
  }
  .service .web { font-family: "Fira Sans", sans-serif; font-style: italic; font-weight: 600; font-size: 20px; margin-top: 4px; }

  .door-transom { position: absolute; left: 477px; top: 9px; width: 170px; height: 150px; background: linear-gradient(180deg, var(--teal-light) 0%, var(--teal-dark) 100%); }
  .door { position: absolute; left: 477px; top: 159px; width: 170px; height: 384px; background: #242424; border: 3px solid #2e2e2e; }
  .door-glass { position: absolute; left: 14px; top: 11px; width: 136px; height: 338px; background: linear-gradient(180deg, var(--teal-light) 0%, var(--teal-mid) 45%, var(--teal-dark) 100%); text-align: center; color: var(--white); }
  .door-glass .door-brand { margin-top: 46px; font-family: "Montserrat", sans-serif; font-weight: 800; font-size: 14px; color: var(--magenta); line-height: 1.2; }
  .door-glass .hours-title { margin-top: 10px; font-family: "Montserrat", sans-serif; font-weight: 600; font-size: 11px; color: var(--hours-red); }
  .door-glass .hours { font-family: "Montserrat", sans-serif; font-weight: 600; font-size: 8px; line-height: 1.35; }
  .door-glass .hours + .hours { margin-top: 6px; }

  .lantern { position: absolute; width: 100px; height: 100px; border-radius: 50%;
    background: radial-gradient(circle, var(--lamp) 0%, rgba(255,210,58,0.55) 22%, rgba(255,210,58,0.12) 50%, rgba(255,210,58,0) 70%); }
  .lantern--left { left: 423px; top: 76px; }
  .lantern--right { left: 601px; top: 76px; }
</style>
</head>
<body>
<div class="canvas">
  <div class="storefront">

    <!-- Upper panes -->
    <div class="pane pane--top" style="left:9px;width:226px;">
      <svg class="awning" viewBox="0 0 226 45" preserveAspectRatio="none" aria-hidden="true">
        <rect x="0" y="0" width="226" height="45" fill="#1c1c1c"/>
        <g fill="#e6e6e6"><path d="M28 0h28v31a14 14 0 0 1-28 0z"/><path d="M84 0h28v31a14 14 0 0 1-28 0z"/><path d="M140 0h28v31a14 14 0 0 1-28 0z"/><path d="M196 0h28v31a14 14 0 0 1-28 0z"/></g>
        <g fill="#0d0d0d"><path d="M0 0h28v31a14 14 0 0 1-28 0z"/><path d="M56 0h28v31a14 14 0 0 1-28 0z"/><path d="M112 0h28v31a14 14 0 0 1-28 0z"/><path d="M168 0h28v31a14 14 0 0 1-28 0z"/></g>
      </svg>
      <div class="headline">ENJOY</div>
    </div>
    <div class="pane pane--top" style="left:243px;width:226px;">
      <svg class="awning" viewBox="0 0 226 45" preserveAspectRatio="none" aria-hidden="true">
        <rect x="0" y="0" width="226" height="45" fill="#1c1c1c"/>
        <g fill="#e6e6e6"><path d="M28 0h28v31a14 14 0 0 1-28 0z"/><path d="M84 0h28v31a14 14 0 0 1-28 0z"/><path d="M140 0h28v31a14 14 0 0 1-28 0z"/><path d="M196 0h28v31a14 14 0 0 1-28 0z"/></g>
        <g fill="#0d0d0d"><path d="M0 0h28v31a14 14 0 0 1-28 0z"/><path d="M56 0h28v31a14 14 0 0 1-28 0z"/><path d="M112 0h28v31a14 14 0 0 1-28 0z"/><path d="M168 0h28v31a14 14 0 0 1-28 0z"/></g>
      </svg>
      <div class="headline">LIFE.</div>
    </div>
    <div class="pane pane--top" style="left:655px;width:226px;">
      <svg class="awning" viewBox="0 0 226 45" preserveAspectRatio="none" aria-hidden="true">
        <rect x="0" y="0" width="226" height="45" fill="#1c1c1c"/>
        <g fill="#e6e6e6"><path d="M28 0h28v31a14 14 0 0 1-28 0z"/><path d="M84 0h28v31a14 14 0 0 1-28 0z"/><path d="M140 0h28v31a14 14 0 0 1-28 0z"/><path d="M196 0h28v31a14 14 0 0 1-28 0z"/></g>
        <g fill="#0d0d0d"><path d="M0 0h28v31a14 14 0 0 1-28 0z"/><path d="M56 0h28v31a14 14 0 0 1-28 0z"/><path d="M112 0h28v31a14 14 0 0 1-28 0z"/><path d="M168 0h28v31a14 14 0 0 1-28 0z"/></g>
      </svg>
      <div class="headline">EAT</div>
    </div>
    <div class="pane pane--top" style="left:889px;width:226px;">
      <svg class="awning" viewBox="0 0 226 45" preserveAspectRatio="none" aria-hidden="true">
        <rect x="0" y="0" width="226" height="45" fill="#1c1c1c"/>
        <g fill="#e6e6e6"><path d="M28 0h28v31a14 14 0 0 1-28 0z"/><path d="M84 0h28v31a14 14 0 0 1-28 0z"/><path d="M140 0h28v31a14 14 0 0 1-28 0z"/><path d="M196 0h28v31a14 14 0 0 1-28 0z"/></g>
        <g fill="#0d0d0d"><path d="M0 0h28v31a14 14 0 0 1-28 0z"/><path d="M56 0h28v31a14 14 0 0 1-28 0z"/><path d="M112 0h28v31a14 14 0 0 1-28 0z"/><path d="M168 0h28v31a14 14 0 0 1-28 0z"/></g>
      </svg>
      <div class="headline">CAKE.</div>
    </div>

    <!-- Lower panes -->
    <div class="pane pane--low" style="left:9px;width:226px;">
      <div class="offer-list">
        <div><span class="custom">Custom</span></div>
        <div class="cake">CAKE</div>
        <div class="holiday">HOLIDAY</div>
        <div class="desserts">DESSERTS</div>
        <div class="cupcakes">CUPCAKES</div>
        <div class="cookies">•COOKIES•</div>
        <div class="amp">&amp;</div>
        <div><span class="sweets">sweets</span></div>
      </div>
      <div class="stripes"><div class="band-magenta"></div><div class="band-dark"></div><div class="band-blush"></div><div class="band-white"></div><div class="band-base"></div></div>
    </div>
    <div class="pane pane--low" style="left:243px;width:226px;">
      <div class="brand-name"><span class="dot"></span>ROSALIND'S<br>Bake House</div>
      <div class="stripes"><div class="band-magenta"></div><div class="band-dark"></div><div class="band-blush"></div><div class="band-white"></div><div class="band-base"></div></div>
    </div>
    <div class="pane pane--low" style="left:655px;width:226px;">
      <div class="brand-name"><span class="dot"></span>ROSALIND'S<br>Bake House</div>
      <div class="stripes"><div class="band-magenta"></div><div class="band-dark"></div><div class="band-blush"></div><div class="band-white"></div><div class="band-base"></div></div>
    </div>
    <div class="pane pane--low" style="left:889px;width:226px;">
      <div class="service">
        <div class="next">NEXT DAY</div>
        <div class="pickup">PICK-UP</div>
        <div class="available">AVAILABLE</div>
        <div class="delivery">DELIVERY</div>
        <div class="order">ORDER ONLINE</div>
        <div class="web">rosalindsbakes.com</div>
      </div>
      <div class="stripes"><div class="band-magenta"></div><div class="band-dark"></div><div class="band-blush"></div><div class="band-white"></div><div class="band-base"></div></div>
    </div>

    <!-- Door -->
    <div class="door-transom"></div>
    <div class="door">
      <div class="door-glass">
        <div class="door-brand">ROSALIND'S<br>Bake House</div>
        <div class="hours-title">HOURS</div>
        <div class="hours">MONDAY-SATURDAY<br>09:00 AM - 02:00 PM</div>
        <div class="hours">SUNDAY<br>11:00 AM - 05:00 PM</div>
      </div>
    </div>

    <div class="lantern lantern--left" role="img" aria-label="Glowing wall lantern beside the door"></div>
    <div class="lantern lantern--right" role="img" aria-label="Glowing wall lantern beside the door"></div>
  </div>
</div>
</body>
</html>
```